Classy, Elegant, Simple Business Card Design

Looking to have a classy, simple, and elegant design. Want a top notch designed business card. I really like the look of the new torvane credit card. I also like the design I attached. I am trying to reach 21-29 year old females for booking us for there wedding or event. We offer Disc Jockey Service, Photo Booth Rentals, and Uplighting .

Target Market(s)

21-28 year old females

Contact Information for Business Card

Has to have logo, website, email, and phone number

Font styles to use
Other font styles liked:
• open to font choice, modern, clean
Designer to choose
33a6d7
0791cd
0555a3
ffffff

Requirements
Must have
• Has to have logo, website, email, and phone number
Nice to have
• I really like the design of the new torvane credit card. I also included my logo and some designs I like
Should not have
• clutter or too much info

```html
<!DOCTYPE html>
<html lang="en">
<head>
<meta charset="utf-8">
<title>Tidelight Events — Business Card</title>
<link rel="stylesheet" href="https://fonts.googleapis.com/css2?family=Arimo:wght@400;700&family=Jost:wght@400;500&display=swap">
<style>
  :root {
    --bg: #efefef;
    --paper: #fdfdfd;
    --sky: #33a6d7;
    --azure: #0791cd;
    --royal: #0555a3;
    --mid: #2a7dc4;
    --white: #ffffff;
  }
  * { margin: 0; padding: 0; box-sizing: border-box; }
  html, body {
    width: 1200px; height: 1200px; overflow: hidden;
    background: var(--bg);
  }
  .canvas { position: relative; width: 1200px; height: 1200px; }

  .card {
    position: absolute;
    width: 614px; height: 397px;
    background: var(--paper);
    overflow: hidden;
  }
  .card--front { left: 478px; top: 175px; }
  .card--back  { left: 150px; top: 624px; }

  .brand {
    position: absolute;
    display: flex; align-items: center; gap: 10px;
    font-family: "Jost", sans-serif;
    font-weight: 500;
    font-size: 26px;
    letter-spacing: 3px;
    color: var(--mid);
    white-space: nowrap;
    transform: translate(-50%, -50%);
  }
  .brand__dot {
    width: 14px; height: 14px; border-radius: 50%;
    background: var(--sky);
  }
  .card--front .brand { left: 51%; top: 44%; }
  .card--back  .brand { left: 73%; top: 30%; }

  .front__band {
    position: absolute;
    left: -6px; bottom: -44px;
    font-family: "Jost", sans-serif;
    font-weight: 500;
    font-size: 128px;
    line-height: 1;
    letter-spacing: 4px;
    color: var(--mid);
    white-space: nowrap;
  }

  .holder {
    position: absolute; left: 68px; top: 228px;
    font-family: "Arimo", sans-serif;
  }
  .holder__name {
    font-size: 23px; font-weight: 700; color: var(--azure);
    line-height: 1.1;
  }
  .holder__role {
    margin-top: 4px;
    font-size: 12px; font-weight: 700; color: var(--royal);
  }

  .contact {
    position: absolute; left: 354px; top: 233px;
    list-style: none;
    font-family: "Arimo", sans-serif;
    font-size: 11.5px; font-weight: 700;
  }
  .contact__row { display: flex; height: 30.5px; }
  .contact__label { width: 24px; color: var(--sky); }
  .contact__value { color: var(--royal); }
</style>
</head>
<body>
<main class="canvas">
  <section class="card card--front">
    <div class="brand"><span class="brand__dot"></span>TIDELIGHT EVENTS</div>
    <div class="front__band">TIDELIGHT</div>
  </section>

  <section class="card card--back">
    <div class="brand"><span class="brand__dot"></span>TIDELIGHT EVENTS</div>
    <div class="holder">
      <p class="holder__name">Marcello</p>
      <p class="holder__role">Photographer</p>
    </div>
    <ul class="contact">
      <li class="contact__row"><span class="contact__label">t:</span><span class="contact__value">78xxxxxxx</span></li>
      <li class="contact__row"><span class="contact__label">m:</span><span class="contact__value">78xxxxxxx</span></li>
      <li class="contact__row"><span class="contact__label">e:</span><span class="contact__value">hello@tidelight.com</span></li>
      <li class="contact__row"><span class="contact__label">w:</span><span class="contact__value">www.tidelight.com</span></li>
    </ul>
  </section>
</main>
</body>
</html>
```